Business Landing Page for SEO Company

Need the landing page of the website designed - I will provide the copy, will need to include details of my company and the services offered, about us, testimonials, faq, etc., and all these elements will need to be arranged graphically on the page.

I want something similar to this: https://torvanequill.com/

Not in terms of color or theme or anything, but we offer a similar service and want to display similar information.

Th services we provide are:

Premium Links
Monthly Links Subscription
Link Insertions

Need to advertise them on the front page. Additionally need a place for testimonials, company details, etc.,

We already have logo for the website. Please use the attached file to insert the logo within the overal design.

Target Market(s)

SEO marketers and agencies

Number of Pages Required

1 page

```html
<!DOCTYPE html>
<html lang="en">
<head>
<meta charset="utf-8">
<title>Torvane – SEO Link Services</title>
<link href="https://fonts.googleapis.com/css2?family=Jost:wght@400;500;600;700&family=Mulish:wght@400;600&display=swap" rel="stylesheet">
<style>
:root{
  --navy:#0b0f4a;
  --navy-deep:#050729;
  --blue:#2f86e4;
  --blue-soft:#e8f1fc;
  --orange:#ff8a00;
  --orange-deep:#f27c00;
  --ink:#2b2b2b;
  --muted:#6d6d6d;
  --white:#ffffff;
  --footer:#2a2a2a;
  --field:#ffffff;
}
*{box-sizing:border-box;margin:0;padding:0}
html,body{width:1200px;height:4380px;overflow:hidden}
body{position:relative;font-family:"Mulish",sans-serif;color:var(--ink);background:var(--white)}
.abs{position:absolute}
.heading{font-family:"Jost",sans-serif;font-weight:400;font-size:46px;line-height:1}
.heading b{font-weight:600}
.btn{position:absolute;display:flex;align-items:center;justify-content:center;border-radius:28px;font-family:"Jost",sans-serif;font-size:16px;color:var(--white);font-weight:500}
.btn-orange{background:var(--orange)}
.btn-blue{background:var(--blue)}
.art{position:absolute;border-radius:24px}

/* Hero */
.hero{position:absolute;left:0;top:0;width:1200px;height:735px;background:radial-gradient(ellipse at 30% 50%,#1d2a9a 0%,var(--navy) 45%,var(--navy-deep) 100%)}
.brand{position:absolute;left:170px;top:18px;font-family:"Jost",sans-serif;font-weight:600;font-size:44px;color:var(--white)}
.nav{position:absolute;right:165px;top:58px;display:flex;gap:22px;font-family:"Jost",sans-serif;font-size:15px;color:var(--white);letter-spacing:.3px}
.nav .active{color:var(--orange)}
.hero-art{left:95px;top:80px;width:540px;height:620px;background:radial-gradient(circle at 45% 45%,#3aa0ff 0%,#2a53c9 40%,rgba(20,25,110,0) 75%)}
.hero-title{position:absolute;left:655px;top:262px;font-family:"Jost",sans-serif;font-weight:600;font-size:58px;color:var(--white)}
.hero-text{position:absolute;left:657px;top:350px;width:380px;font-size:19px;line-height:1.35;color:var(--white)}

/* About */
.about-title{left:170px;top:845px;color:var(--blue)}
.about-title b{color:var(--orange)}
.about-text{position:absolute;left:172px;width:390px;font-size:12.5px;line-height:1.6;color:var(--muted)}
.about-art{left:655px;top:880px;width:380px;height:330px;background:linear-gradient(135deg,#eef4fd,#cfe0f7)}

/* Services */
.services{position:absolute;left:0;top:1300px;width:1200px;height:720px;background:var(--blue)}
.services-title{left:0;width:1200px;top:1440px;text-align:center;color:var(--white)}
.card{position:absolute;top:1545px;width:245px;height:360px;background:var(--white);border-radius:32px;box-shadow:0 14px 24px rgba(0,0,0,.18);text-align:center}
.card svg{margin-top:40px}
.card h3{font-family:"Jost",sans-serif;font-weight:500;font-size:16px;margin-top:26px;color:var(--ink)}
.card p{font-size:11.5px;line-height:1.5;color:var(--muted);margin:14px 28px 0}
.card .btn{left:72px;top:270px;width:100px;height:44px;font-size:14px}

/* Testimonials */
.testi-art{left:150px;top:2060px;width:370px;height:380px;background:linear-gradient(135deg,#f2f6fd,#d8e5f8)}
.testi-title{left:580px;top:2130px;color:var(--blue)}
.testi-title b{color:var(--orange)}
.testi-text{position:absolute;left:582px;top:2196px;width:420px;font-size:13px;line-height:1.65;color:var(--muted)}
.testi-name{position:absolute;left:582px;top:2322px;font-family:"Jost",sans-serif;font-weight:600;font-size:17px;color:var(--orange)}
.testi-role{position:absolute;left:582px;top:2350px;font-size:14px;color:var(--ink)}

/* FAQ */
.faq-title{left:170px;top:2488px;color:var(--blue)}
.faq-title b{color:var(--orange)}
.faq-item{position:absolute;left:170px;width:520px;background:var(--white);border-radius:26px;box-shadow:0 4px 14px rgba(0,0,0,.14);font-size:15px;color:var(--ink)}
.faq-item .q{position:absolute;left:22px;top:16px}
.faq-item .a{position:absolute;left:22px;top:62px;width:420px;font-size:11.5px;line-height:1.55;color:var(--muted)}
.faq-item .toggle{position:absolute;right:0;top:4px}
.faq-art{left:740px;top:2500px;width:290px;height:400px;background:linear-gradient(160deg,#f4f7fc,#dbe6f6)}

/* Contact form */
.contact{position:absolute;left:0;top:3080px;width:1200px;height:760px;background:linear-gradient(135deg,var(--orange) 0%,var(--orange-deep) 100%)}
.contact-title{left:0;width:1200px;top:3230px;text-align:center;color:var(--white)}
.field{position:absolute;background:var(--field);border-radius:24px;font-size:13px;color:var(--ink);padding:22px 22px}
.field.short{padding-top:21px}

/* Footer */
.footer{position:absolute;left:0;top:3830px;width:1200px;height:550px;background:var(--footer)}
.foot-title{left:170px;top:3940px;color:var(--white)}
.foot-row{position:absolute;left:170px;display:flex;align-items:center;gap:16px;font-size:21px;color:var(--white)}
.foot-brand{position:absolute;left:700px;top:3975px;font-family:"Jost",sans-serif;font-weight:600;font-size:108px;line-height:1;color:var(--white)}
.foot-rule{position:absolute;left:170px;top:4280px;width:860px;height:1px;background:#5a5a5a}
.copyright{position:absolute;left:0;width:1200px;top:4305px;text-align:center;font-size:14px;color:var(--white)}
</style>
</head>
<body>

<!-- Hero -->
<section class="hero">
  <div class="brand">torvane</div>
  <nav class="nav">
    <span class="active">HOME</span><span>ABOUT US</span><span>FAQ</span><span>OUR SERVICES</span><span>BLOG</span><span>CONTACT US</span>
  </nav>
  <div class="art hero-art" role="img" aria-label="Illustration of a large monitor with analytics screens and a magnifying glass"></div>
  <h1 class="hero-title">Torvane</h1>
  <p class="hero-text">Nemo enim ipsam voluptatem quia voluptas aspernatur aut odit aut fugit, sed quia</p>
  <div class="btn btn-orange" style="left:657px;top:450px;width:122px;height:50px">Read More</div>
</section>

<!-- About -->
<h2 class="heading abs about-title">About <b>Torvane</b></h2>
<p class="about-text" style="top:920px">Nam libero tempore, cum soluta nobis est eligendi optio cumque nihil impedit quo minus id quod maxime placeat facere possimus omnis voluptas assumenda est, omnis dolor repellendus. Temporibus autem quibusdam et aut officiis debitis aut rerum necessitatibus saepe eveniet ut et voluptates repudiandae sint et molestiae non recusandae.</p>
<p class="about-text" style="top:1070px">At vero eos et accusamus et iusto odio dignissimos ducimus qui blanditiis praesentium voluptatum deleniti atque corrupti quos dolores et quas molestias excepturi sint occaecati cupiditate non provident.</p>
<div class="btn btn-orange" style="left:172px;top:1170px;width:120px;height:50px;font-size:14px">READ MORE</div>
<div class="art about-art" role="img" aria-label="Illustration of two people working beside large dashboard charts"></div>

<!-- Services -->
<section class="services"></section>
<svg class="abs" style="left:0;top:1290px" width="1200" height="60" viewBox="0 0 1200 60" aria-hidden="true">
  <path d="M0 0H1200V34C1170 10 1140 10 1110 30C1080 8 1040 8 1010 30C980 6 940 6 910 30C880 10 840 10 810 32C780 8 740 8 710 30C680 6 640 6 610 32C580 10 540 10 510 30C480 6 440 6 410 30C380 10 340 10 310 32C280 8 240 8 210 30C180 6 140 6 110 30C80 10 40 10 0 34Z" fill="#ffffff"/>
</svg>
<h2 class="heading abs services-title" style="color:var(--white)">Our <b>Services</b></h2>

<article class="card" style="left:180px">
  <svg width="52" height="52" viewBox="0 0 52 52" fill="none" stroke="#2f86e4" stroke-width="2.5"><circle cx="24" cy="28" r="20"/><circle cx="24" cy="28" r="12"/><circle cx="24" cy="28" r="4" fill="#ff8a00" stroke="none"/><path d="M24 28L46 6M40 4L46 6L48 12"/></svg>
  <h3>PREMIUM LINKS</h3>
  <p>Nam libero tempore, cum soluta nobis est eligendi optio cumque nihil impedit quo minus id quod maxime.</p>
  <div class="btn btn-blue">READ MORE</div>
</article>
<article class="card" style="left:470px">
  <svg width="52" height="52" viewBox="0 0 52 52" fill="none" stroke="#ff8a00" stroke-width="2.5"><path d="M30 8C40 6 46 12 44 22L26 40L12 26Z"/><circle cx="33" cy="19" r="4"/><path d="M12 26L6 24L14 16L22 16M26 40L28 46L36 38L36 30M10 36L4 48L16 42"/></svg>
  <h3>MONTHLY LINKS SUBSCRIPTION</h3>
  <p>Nam libero tempore, cum soluta nobis est eligendi optio cumque nihil impedit quo minus id quod maxime.</p>
  <div class="btn btn-orange">READ MORE</div>
</article>
<article class="card" style="left:760px">
  <svg width="52" height="52" viewBox="0 0 52 52" fill="none" stroke="#2f86e4" stroke-width="2.5"><rect x="6" y="6" width="40" height="30" rx="3"/><path d="M18 46H34M26 36V46M18 28L26 12L34 28M21 22H31"/></svg>
  <h3>LINK INSERTIONS</h3>
  <p>Nam libero tempore, cum soluta nobis est eligendi optio cumque nihil impedit quo minus id quod maxime.</p>
  <div class="btn btn-blue">READ MORE</div>
</article>

<!-- Testimonials -->
<div class="art testi-art" role="img" aria-label="Isometric illustration of SEO tools with people and large letters"></div>
<h2 class="heading abs testi-title">Our <b>Testimonials</b></h2>
<p class="testi-text">Quis autem vel eum iure reprehenderit qui in ea voluptate velit esse quam nihil molestiae consequatur, vel illum qui dolorem eum fugiat quo voluptas nulla pariatur. Quis autem vel eum iure reprehenderit qui in ea voluptate velit esse quam nihil mo lestiae consequatur.</p>
<div class="testi-name">– Dana Whitfield</div>
<div class="testi-role">Manager</div>

<!-- FAQ -->
<h2 class="heading abs faq-title">Our <b>FAQ</b></h2>
<div class="faq-item" style="top:2560px;height:52px">
  <span class="q">Lorem ipsum dolor sit amet, adipiscing?</span>
  <svg class="toggle" width="44" height="44" viewBox="0 0 44 44"><circle cx="22" cy="22" r="22" fill="#2f86e4"/><path d="M22 13V31M13 22H31" stroke="#fff" stroke-width="3"/></svg>
</div>
<div class="faq-item" style="top:2628px;height:126px">
  <span class="q">At vero eos et accusamus et iusto odio?</span>
  <p class="a">Nemo enim ipsam voluptatem quia voluptas sit aspernatur aut odit aut fugit, sed quia consequuntur magni dolores eos qui ratione.</p>
  <svg class="toggle" width="44" height="44" viewBox="0 0 44 44"><circle cx="22" cy="22" r="22" fill="#2f86e4"/><path d="M13 22H31" stroke="#fff" stroke-width="3"/></svg>
</div>
<div class="faq-item" style="top:2770px;height:52px">
  <span class="q">Itaque earum rerum hic tenetur a sapiente?</span>
  <svg class="toggle" width="44" height="44" viewBox="0 0 44 44"><circle cx="22" cy="22" r="22" fill="#2f86e4"/><path d="M22 13V31M13 22H31" stroke="#fff" stroke-width="3"/></svg>
</div>
<div class="faq-item" style="top:2838px;height:52px">
  <span class="q">Voluptatibus maiores alias consequatur?</span>
  <svg class="toggle" width="44" height="44" viewBox="0 0 44 44"><circle cx="22" cy="22" r="22" fill="#2f86e4"/><path d="M22 13V31M13 22H31" stroke="#fff" stroke-width="3"/></svg>
</div>
<div class="art faq-art" role="img" aria-label="Illustration of SEO symbols with a rocket, gears, target and magnifier"></div>

<!-- Contact form -->
<section class="contact" role="img" aria-label="Orange tinted office scene background"></section>
<svg class="abs" style="left:0;top:3070px" width="1200" height="60" viewBox="0 0 1200 60" aria-hidden="true">
  <path d="M0 0H1200V34C1170 10 1140 10 1110 30C1080 8 1040 8 1010 30C980 6 940 6 910 30C880 10 840 10 810 32C780 8 740 8 710 30C680 6 640 6 610 32C580 10 540 10 510 30C480 6 440 6 410 30C380 10 340 10 310 32C280 8 240 8 210 30C180 6 140 6 110 30C80 10 40 10 0 34Z" fill="#ffffff"/>
</svg>
<h2 class="heading abs contact-title" style="color:var(--white)">Contact <b>Form</b></h2>
<div class="field short" style="left:210px;top:3345px;width:380px;height:62px">Name</div>
<div class="field short" style="left:610px;top:3345px;width:380px;height:62px">Phone</div>
<div class="field short" style="left:210px;top:3430px;width:780px;height:62px">Email</div>
<div class="field" style="left:210px;top:3520px;width:780px;height:140px">Message</div>
<div class="btn btn-blue" style="left:535px;top:3690px;width:130px;height:54px;font-size:17px">Submit</div>

<!-- Footer -->
<footer class="footer"></footer>
<h2 class="heading abs foot-title" style="color:var(--white)">Contact <b>Us</b></h2>
<div class="foot-row" style="top:4050px">
  <svg width="48" height="48" viewBox="0 0 48 48" fill="none" stroke="#fff" stroke-width="2"><circle cx="24" cy="24" r="22"/><path d="M17 14L21 14L23 20L20 22C21 25 23 27 26 28L28 25L34 27L34 31C34 33 32 34 30 34C22 33 15 26 14 18C14 16 15 14 17 14Z"/></svg>
  <span>+123 555 0142</span>
</div>
<div class="foot-row" style="top:4112px">
  <svg width="48" height="48" viewBox="0 0 48 48" fill="none" stroke="#fff" stroke-width="2"><circle cx="24" cy="24" r="22"/><rect x="13" y="16" width="22" height="16" rx="2"/><path d="M13 17L24 26L35 17"/></svg>
  <span>info@torvane.com</span>
</div>
<div class="foot-row" style="top:4174px">
  <svg width="48" height="48" viewBox="0 0 48 48" fill="none" stroke="#fff" stroke-width="2"><circle cx="24" cy="24" r="22"/><path d="M24 36C24 36 15 27 15 21A9 9 0 0 1 33 21C33 27 24 36 24 36Z"/><circle cx="24" cy="21" r="3"/></svg>
  <span>Quill Lane, Harbor City</span>
</div>
<div class="foot-brand">torvane</div>
<div class="foot-rule"></div>
<p class="copyright">Copyright @ 2021 Torvane. All Rights Reserved.</p>

</body>
</html>
```